Bring me business with this creative business card

Design my new business card. I am looking for something different with an impact. People will take a look at this card & they will 1- see how different & creative I am, 2-understand what I do 3- Call me to meet me!

I make videos with a message, testimonials. I am dynamic, fun, creative & human. My new website is in construction but in the meantime you can check this old one: brightpath.ca & another one Tidebloom.com & tidebloom facebook page.
I make videos. sometimes with a cameraman, sometimes with my phone. As an ex Public Relations agent, the message is the most important thing for me. I want to make my clients shine! When they start with me they often remind me of a lamb, when I finish coaching them they are powerful like LIONS! That's why I need a powerful business card!

Target Market(s)

Entrepreneurs, solo entrepreneurs, small & medium companies & start ups. People i will meet while networking. People that need videos on their website & social Networks to get attention, to be visible. men & women. From 35 to 49 years old.
I am an ex Public relations agent. I used to send clients in traditional medias, now with videos they have more chances to be seen on google the new media. I do videos of the president, his team, his loyal clients saying how great the company is & expert videos like series so people can be seen for example every 1 st of every month with a short 2 minute video. Also with my 20 years in marketing & communications I can coach & give tips to anybody who needs it.
Target: anybody who would like my old website brightpath.ca & I also have another website but it will be off line soon: tidebloom.com could give you ideas.

Industry/Entity Type

Communications

Contact Information for Business Card

I am in Montreal,So the business cards have to be the usual size like we have in Montreal: 9 cm x 5 cm
Details:My text: Mathilde Tessier Communication coach/Chief Lion. "Videos that carry your own voice" off: 514-555-0147 cell: 514-555-0183. tidebloom.com
mathilde@tidebloom.com logo facebook, youtube, instagram

Colors
f37122

Requirements
Must have
• Dynamic, happy. Orange. Be creative in the look but NOT the shape of the card. Easy to read. Big enough to read.
Should not have
• No funny shapes: no round, no square, just the usual. I love creative but NOT on shape.

```html
<!DOCTYPE html>
<html lang="en">
<head>
<meta charset="utf-8">
<title>Tidebloom business card</title>
<link rel="stylesheet" href="https://fonts.googleapis.com/css2?family=Roboto:wght@400;500;700&display=swap">
<style>
  :root {
    --orange: #f37122;
    --orange-deep: #ee5f1c;
    --amber: #f6a21c;
    --ink: #5f5f5f;
    --paper: #ffffff;
    --ground: #ebe8e3;
  }
  * { margin: 0; padding: 0; box-sizing: border-box; }
  html, body { width: 1200px; height: 911px; overflow: hidden; }
  body {
    background: var(--ground);
    font-family: "Roboto", Arial, sans-serif;
    position: relative;
  }
  .card {
    position: absolute;
    width: 540px;
    height: 300px;
    background: var(--paper);
    box-shadow: 0 6px 18px rgba(0,0,0,.18);
    overflow: hidden;
  }
  /* front */
  .card--front { left: 40px; top: 305px; }
  .front__band {
    position: absolute; left: 0; top: 0; width: 100%; height: 64px;
    background: linear-gradient(90deg, var(--orange-deep), var(--orange));
  }
  .front__mark {
    position: absolute; left: 50%; top: 24px; width: 80px; height: 80px;
    margin-left: -40px; border-radius: 50%;
    background: var(--amber); border: 3px solid var(--paper);
  }
  .front__body {
    position: absolute; left: 0; right: 0; top: 122px; text-align: center;
  }
  .front__name {
    color: var(--orange); font-weight: 700; font-size: 22px; letter-spacing: .5px;
    text-transform: uppercase;
  }
  .front__title {
    color: var(--amber); font-weight: 500; font-size: 13px; letter-spacing: .6px;
    text-transform: uppercase; margin-top: 4px;
  }
  .front__contacts {
    list-style: none; margin-top: 14px; color: var(--ink); font-size: 13px; line-height: 1.6;
  }
  .front__contacts b { color: var(--orange); font-weight: 700; }
  /* back */
  .card--back { left: 620px; top: 305px; }
  .back__lockup {
    position: absolute; left: 0; right: 0; top: 38px;
    display: flex; flex-direction: column; align-items: center;
  }
  .back__mark { width: 88px; height: 88px; border-radius: 50%; background: var(--amber); }
  .back__name {
    margin-top: 12px; color: var(--orange); font-weight: 500; font-size: 34px; letter-spacing: 4px;
  }
  .back__rule-line {
    display: flex; align-items: center; gap: 10px; margin-top: 4px;
    color: var(--amber); font-size: 12px; letter-spacing: 2px;
  }
  .back__rule-line::before, .back__rule-line::after {
    content: ""; width: 44px; height: 1px; background: var(--amber);
  }
  .back__tagline { margin-top: 8px; color: var(--orange); font-weight: 500; font-size: 14px; }
  .back__social { display: flex; gap: 8px; margin-top: 12px; align-items: center; }
  .back__social::before, .back__social::after {
    content: ""; width: 60px; height: 1px; background: var(--orange);
  }
  .social-dot { width: 16px; height: 16px; border-radius: 50%; background: var(--orange); }
</style>
</head>
<body>
  <section class="card card--front" aria-label="Business card front">
    <div class="front__band"></div>
    <div class="front__mark"></div>
    <div class="front__body">
      <h1 class="front__name">Mathilde T.</h1>
      <p class="front__title">Communication Coach Lead Creator</p>
      <ul class="front__contacts">
        <li><b>P:</b> 514-555-0147 <b>C:</b> 514-555-0183</li>
        <li><b>E:</b> mathilde@tidebloom.com</li>
        <li><b>W:</b> www.tidebloom.com</li>
      </ul>
    </div>
  </section>

  <section class="card card--back" aria-label="Business card back">
    <div class="back__lockup">
      <div class="back__mark"></div>
      <p class="back__name">TIDEBLOOM</p>
      <p class="back__rule-line">| VIDEO | MESSAGE</p>
      <p class="back__tagline">Videos that carry your own voice</p>
      <div class="back__social">
        <span class="social-dot"></span>
        <span class="social-dot"></span>
        <span class="social-dot"></span>
      </div>
    </div>
  </section>
</body>
</html>
```